Keystonery Billboard - Financial Services Company (Investments, Tax Planning and Insurance)

Our new office has a billboard directly above the office building. We'd like something eye-catching with a strong Call to Action, with the main part of the billboard being under 7 words if possible. We'd like you to include a way to get ahold of us (either our website keystoneryllc.example or our phone number 302-418-2907. You may also include in small font something to indicate that we've been serving the area since 1980 (the DE area, the tri-state area, the Marlowe Hollow, etc.)

We offer financial planning, tax planning, and insurance, and we help our clients to focus on their goals and happiness by providing everything they need for lifelong wealth under one roof.

Our logos are attached, we use a triangle logo with green and gray. We use the tagline "discover lasting prosperity" but this does not need to be included.

Potential ideas we have seen from other financial companies-
- the concept that the driver spends more time looking at billboards than planning for their retirement
-something along the lines of "everything you need for your finances is in this building right here" planning, investments, taxes, insurance"
-don't spend your time worrying about retirement, let us help you plan for it
-are you working for your money, or is it working for you?
- retirement takes planning, we're here to help
- ready to retire? talk to us
- need investment advice?
- need help investing?
- crossing your fingers isn't a retirement plan. we can help.
- retiring soon? you need help.

Those are just general ideas, please feel free to be creative.

brand colors:
#00b585
#00b185
#000000
#ffffff
#6d6f75
#6d6f75
#6f7074
#021712
#052e24

```html
<!DOCTYPE html>
<html lang="en">
<head>
<meta charset="utf-8">
<title>Keystonery Billboard</title>
<link rel="stylesheet" href="https://fonts.googleapis.com/css2?family=Bebas+Neue&family=Poppins:wght@500;600;800&display=swap">
<style>
  :root {
    --green: #00b585;
    --green-deep: #00a06f;
    --ink: #333333;
    --black: #1c1c1c;
    --black-soft: #2c2c2c;
    --white: #ffffff;
    --gray: #6d6f75;
    --page: #f4f4f4;
  }
  * { box-sizing: border-box; margin: 0; padding: 0; }
  html, body { width: 835px; height: 1200px; overflow: hidden; }
  body { background: var(--page); font-family: "Poppins", sans-serif; position: relative; }

  .billboard {
    position: absolute; left: 29px; top: 486px;
    width: 777px; height: 228px;
    background: var(--white);
    box-shadow: 0 6px 18px rgba(0,0,0,0.18);
  }
  .headline-band {
    position: absolute; left: 0; top: 0; width: 100%; height: 114px;
    background: radial-gradient(ellipse at 40% 30%, var(--black-soft), var(--black) 70%);
  }
  .headline {
    position: absolute; left: 0; right: 0; top: 14px;
    text-align: center;
    font-family: "Bebas Neue", sans-serif;
    font-size: 80px; line-height: 1; letter-spacing: 0.5px;
    color: var(--white);
    white-space: nowrap;
  }
  .headline .cta { color: var(--green); }

  .services { position: absolute; top: 104px; left: 26px; right: 38px; height: 48px; }
  .service {
    position: absolute; top: 0; height: 48px;
    display: flex; align-items: center; justify-content: center; gap: 8px;
    background: var(--white);
    border: 2px solid var(--green);
    border-radius: 12px;
    box-shadow: 0 0 0 3px var(--white);
    font-weight: 800; font-size: 22px; color: var(--ink);
    letter-spacing: 0.2px;
  }
  .service svg { width: 30px; height: 30px; flex: none; }
  .service--investments { left: 0; width: 228px; }
  .service--tax { left: 247px; width: 236px; }
  .service--insurance { left: 502px; width: 211px; }

  .brand {
    position: absolute; left: 26px; top: 160px;
    display: flex; flex-direction: column;
  }
  .brand-row { display: flex; align-items: center; gap: 10px; }
  .brand-square { width: 22px; height: 22px; background: var(--green); }
  .brand-name { font-weight: 600; font-size: 36px; line-height: 1; color: var(--green-deep); }
  .brand-tagline {
    margin-top: 4px; margin-left: 32px;
    font-weight: 500; font-size: 7.5px; letter-spacing: 3px;
    color: var(--gray); text-transform: uppercase;
  }

  .contact {
    position: absolute; right: 30px; top: 158px;
    display: flex; align-items: center; gap: 14px;
  }
  .contact svg { width: 30px; height: 30px; }
  .phone { font-weight: 800; font-size: 52px; line-height: 1; color: var(--ink); letter-spacing: 0.5px; }
</style>
</head>
<body>
  <main class="billboard">
    <div class="headline-band">
      <h1 class="headline">Ready to retire? <span class="cta">Talk to us</span></h1>
    </div>

    <ul class="services">
      <li class="service service--investments">
        <svg viewBox="0 0 30 30" aria-hidden="true">
          <rect x="2" y="18" width="3.5" height="10" fill="var(--green)"/>
          <rect x="7.5" y="14" width="3.5" height="14" fill="var(--green)"/>
          <rect x="13" y="10" width="3.5" height="18" fill="var(--green)"/>
          <path d="M14.75 2 L10 7 H13 V9 H16.5 V7 H19.5 Z" fill="var(--green)"/>
          <circle cx="22" cy="20" r="7" fill="none" stroke="var(--green)" stroke-width="2.2"/>
          <text x="22" y="24" text-anchor="middle" font-family="Poppins, sans-serif" font-weight="800" font-size="10" fill="var(--green)">$</text>
        </svg>
        INVESTMENTS
      </li>
      <li class="service service--tax">
        <svg viewBox="0 0 30 30" aria-hidden="true">
          <rect x="3" y="2" width="15" height="25" rx="1.5" fill="none" stroke="var(--green)" stroke-width="2"/>
          <circle cx="9" cy="8" r="3" fill="var(--green)"/>
          <line x1="6" y1="14" x2="15" y2="14" stroke="var(--green)" stroke-width="1.8"/>
          <line x1="6" y1="18" x2="15" y2="18" stroke="var(--green)" stroke-width="1.8"/>
          <line x1="6" y1="22" x2="13" y2="22" stroke="var(--green)" stroke-width="1.8"/>
          <rect x="16" y="12" width="12" height="16" rx="1.5" fill="var(--white)" stroke="var(--green)" stroke-width="2"/>
          <rect x="18.5" y="14.5" width="7" height="3" fill="var(--green)"/>
          <g fill="var(--green)">
            <rect x="18.5" y="19.5" width="2" height="2"/><rect x="21.5" y="19.5" width="2" height="2"/><rect x="24.5" y="19.5" width="1.5" height="2"/>
            <rect x="18.5" y="23" width="2" height="2"/><rect x="21.5" y="23" width="2" height="2"/><rect x="24.5" y="23" width="1.5" height="2"/>
          </g>
        </svg>
        TAX PLANNING
      </li>
      <li class="service service--insurance">
        <svg viewBox="0 0 30 30" aria-hidden="true">
          <path d="M15 2 L26 6 V14 C26 21 21 26 15 28 C9 26 4 21 4 14 V6 Z" fill="var(--green)"/>
          <path d="M15 6 L22 8.6 V14 C22 18.6 19 22 15 23.6 C11 22 8 18.6 8 14 V8.6 Z" fill="var(--white)"/>
          <path d="M11 15 L14 18 L19.5 11.5" fill="none" stroke="var(--green)" stroke-width="2.4" stroke-linecap="round" stroke-linejoin="round"/>
        </svg>
        &nbsp;&nbsp;INSURANCE
      </li>
    </ul>

    <div class="brand">
      <div class="brand-row">
        <span class="brand-square" aria-hidden="true"></span>
        <span class="brand-name">Keystonery</span>
      </div>
      <span class="brand-tagline">Discover lasting prosperity</span>
    </div>

    <div class="contact">
      <svg viewBox="0 0 30 30" aria-hidden="true">
        <path d="M8 3 C6 3 3 5.5 3.5 9 C5 18 12 25 21 26.5 C24.5 27 27 24 27 22 L26.5 20.5 L21 18 L18.5 20.5 C15 19 11 15 9.5 11.5 L12 9 L9.5 3.5 Z" fill="var(--green)"/>
        <path d="M17 4 A9 9 0 0 1 26 13" fill="none" stroke="var(--green)" stroke-width="2.2" stroke-linecap="round"/>
        <path d="M17 8.5 A4.5 4.5 0 0 1 21.5 13" fill="none" stroke="var(--green)" stroke-width="2.2" stroke-linecap="round"/>
      </svg>
      <span class="phone">302-418-2907</span>
    </div>
  </main>
</body>
</html>
```